Communication and Marketing agency needs a new presentation card

We are a group of communication and marketing agencies specialized in companies that are in the logistics and industrial sector. The head agency is TELVANO Grupo and the group consists of 4 agencies: TELVANO Media, TELVANO Digital, TELVANO Research and DifundeEnPantalla. We hace 4 offices in Spain (Madrid, Barcelona, Valencia and Murcia). We are looking for a clean and attractive design that transmits our experience, brand presence in the market and knowledge to those who receive the card.It has to maintain the colors of the logo that is attached.
Target Market(s)
logistics and industrial sector
Marketing department
Contact Information for Business Card
Clean and attractive design

```html
<!DOCTYPE html>
<html lang="es">
<head>
<meta charset="utf-8">
<title>TELVANO Grupo – Business Card</title>
<link href="https://fonts.googleapis.com/css2?family=Questrial&display=swap" rel="stylesheet">
<style>
  :root{
    --stage:#2b2b2c;
    --card-grey:#59595b;
    --brand-red:#b21d27;
    --white:#ffffff;
    --ink-grey:#4a4a4c;
  }
  *{margin:0;padding:0;box-sizing:border-box}
  html,body{width:1200px;height:892px;overflow:hidden}
  body{background:var(--stage);font-family:"Questrial",sans-serif;position:relative}
  .card{position:absolute;top:271px;width:540px;height:350px;border-radius:4px;overflow:hidden;box-shadow:0 10px 30px rgba(0,0,0,.45)}

  /* Back card */
  .card-back{left:40px;background:var(--card-grey);color:var(--white)}
  .group-name{position:absolute;left:0;right:0;top:110px;text-align:center;font-size:52px;letter-spacing:3px;line-height:1}
  .group-name .suffix{font-size:30px;letter-spacing:1px}
  .agency-list{position:absolute;left:24px;right:24px;bottom:52px;display:flex;justify-content:space-between;align-items:flex-end}
  .agency{font-size:15px;letter-spacing:.5px;text-align:center;line-height:1.15}
  .agency small{display:block;font-size:11px}

  /* Front card */
  .card-front{left:620px;background:var(--white)}
  .front-shapes{position:absolute;inset:0}
  .agency-name{position:absolute;left:0;right:0;top:70px;text-align:center;color:var(--brand-red);font-size:50px;letter-spacing:3px;line-height:1}
  .agency-name .suffix{font-size:30px;letter-spacing:1px}
  .holder{position:absolute;left:30px;top:238px;color:var(--white)}
  .holder-name{font-size:24px;line-height:1.1}
  .holder-role{font-size:16px}
  .contact{position:absolute;right:20px;top:200px;list-style:none;color:var(--white);font-size:13.5px;line-height:19px;text-align:right}
  .contact li{display:flex;justify-content:flex-end;align-items:center;gap:7px}
  .contact svg{width:12px;height:12px;flex:none}
  .offices{position:absolute;right:26px;bottom:12px;color:var(--white);font-size:15px;letter-spacing:.5px}
</style>
</head>
<body>

<section class="card card-back" aria-label="Card back">
  <div class="group-name">TELVANO <span class="suffix">Grupo</span></div>
  <div class="agency-list">
    <div class="agency">TELVANO<small>Digital</small></div>
    <div class="agency">TELVANO<small>Media</small></div>
    <div class="agency">TELVANO<small>Research</small></div>
    <div class="agency">Difunde<small>EnPantalla</small></div>
  </div>
</section>

<section class="card card-front" aria-label="Card front">
  <svg class="front-shapes" viewBox="0 0 540 350" width="540" height="350" aria-hidden="true">
    <path d="M0 214 L160 200 L170 180 L185 198 L540 170 L540 300 L0 300 Z" fill="var(--brand-red)"/>
    <rect x="0" y="300" width="540" height="50" fill="var(--card-grey)"/>
    <line x1="0" y1="304" x2="540" y2="304" stroke="var(--white)" stroke-width="1.5"/>
  </svg>

  <div class="agency-name">TELVANO <span class="suffix">Media</span></div>

  <div class="holder">
    <div class="holder-name">Ramiro Castell</div>
    <div class="holder-role">Director</div>
  </div>

  <ul class="contact">
    <li>910 472 318
      <svg viewBox="0 0 12 12"><path d="M2 1h2.5l1 3-1.5 1a6 6 0 0 0 3 3l1-1.5 3 1V11a1 1 0 0 1-1 1A10 10 0 0 1 1 2a1 1 0 0 1 1-1z" fill="#fff"/></svg></li>
    <li>655 201 774
      <svg viewBox="0 0 12 12"><rect x="3" y="0.5" width="6" height="11" rx="1" fill="none" stroke="#fff"/><circle cx="6" cy="9.5" r=".7" fill="#fff"/></svg></li>
    <li>rcastell@telvano.es
      <svg viewBox="0 0 12 12"><rect x="0.5" y="2.5" width="11" height="7" fill="none" stroke="#fff"/><path d="M.5 2.5 6 7l5.5-4.5" fill="none" stroke="#fff"/></svg></li>
    <li>ramirocastell
      <svg viewBox="0 0 12 12"><rect x="1" y="1" width="10" height="10" fill="#fff"/></svg></li>
    <li>www.telvano.es
      <svg viewBox="0 0 12 12"><circle cx="6" cy="6" r="5.3" fill="none" stroke="#fff"/><path d="M.7 6h10.6M6 .7c-3 3-3 7.6 0 10.6M6 .7c3 3 3 7.6 0 10.6" fill="none" stroke="#fff" stroke-width=".8"/></svg></li>
  </ul>

  <div class="offices">Madrid &bull; Barcelona &bull; Valencia &bull; Murcia</div>
</section>

</body>
</html>
```